Coastline Premier Retreats Business Card Design

Design a business card for Coastline Premier Retreats. Look at the website for colors and reference. Card should have logo, name, title, office number, mobile number, email, URL and a tagline like, "Luxury Hotel & Resort Email Marketing" (This might change).

https://www.coastlinepremierretreats.example

The rest I will leave up to your imagination.

Contact Information for Business Card

Logo, name, title, office number, mobile number, email, URL and a tagline like, "Luxury Hotel & Resort Email Marketing" (This might change).

```html
<!DOCTYPE html>
<html lang="en">
<head>
<meta charset="utf-8">
<title>Coastline Premier Retreats – Business Card</title>
<link href="https://fonts.googleapis.com/css2?family=Montserrat:ital,wght@0,400;0,500;0,700;0,800;1,500&display=swap" rel="stylesheet">
<style>
  :root {
    --stage: #2b2b2b;
    --card: #1b1b1b;
    --orange: #f07814;
    --white: #ffffff;
    --ink-soft: #e6e6e6;
    --emboss: #3a3a3a;
  }
  * { box-sizing: border-box; margin: 0; padding: 0; }
  html, body {
    width: 1200px; height: 900px; overflow: hidden;
    background: var(--stage);
    font-family: "Montserrat", sans-serif;
  }
  .canvas {
    width: 1200px; height: 900px;
    display: flex; flex-direction: column; align-items: center; justify-content: center;
    gap: 36px;
  }
  .card {
    position: relative;
    width: 700px; height: 400px;
    background: var(--card);
    overflow: hidden;
    box-shadow: 0 10px 30px rgba(0,0,0,.45);
  }

  /* Front */
  .brand {
    position: absolute; left: 150px; top: 48px;
    display: flex; align-items: center; gap: 12px;
  }
  .brand-mark { width: 18px; height: 18px; background: var(--orange); flex: none; }
  .brand-name {
    color: var(--white); font-weight: 800; font-size: 24px;
    letter-spacing: 1px; text-transform: uppercase; line-height: 1;
    white-space: nowrap;
  }
  .address {
    position: absolute; left: 150px; top: 118px;
    color: var(--ink-soft); font-size: 14px; line-height: 1.45; letter-spacing: .4px;
  }
  .contacts {
    position: absolute; left: 128px; top: 176px;
    list-style: none; color: var(--ink-soft); font-size: 14px; line-height: 1.55; letter-spacing: .4px;
  }
  .contacts li { display: flex; align-items: center; gap: 8px; white-space: nowrap; }
  .contacts svg { width: 13px; height: 13px; fill: var(--orange); flex: none; }
  .contacts .url-domain { color: var(--orange); }
  .person {
    position: absolute; right: 62px; top: 296px; text-align: right;
  }
  .person-name {
    color: var(--orange); font-weight: 700; font-size: 28px; letter-spacing: 1.5px;
    text-transform: uppercase; line-height: 1.1; white-space: nowrap;
  }
  .person-title { color: var(--ink-soft); font-size: 15px; letter-spacing: .5px; margin-top: 2px; }
  .accent-tab {
    position: absolute; right: 0; top: 300px; width: 22px; height: 50px; background: var(--orange);
  }
  .base-band {
    position: absolute; left: 0; bottom: 0; width: 100%; height: 26px; background: var(--orange);
  }

  /* Back */
  .card-back {
    display: flex; flex-direction: column; align-items: center; justify-content: center; gap: 34px;
  }
  .back-brand { display: flex; align-items: center; gap: 16px; }
  .back-brand .brand-mark { width: 24px; height: 24px; background: var(--emboss); }
  .back-brand .brand-name { color: var(--emboss); font-size: 30px; }
  .tagline {
    color: var(--orange); font-style: italic; font-weight: 500; font-size: 22px; letter-spacing: .5px;
    white-space: nowrap;
  }
</style>
</head>
<body>
<main class="canvas">

  <section class="card card-front" aria-label="Business card front">
    <div class="brand">
      <span class="brand-mark"></span>
      <span class="brand-name">Coastline Premier Retreats</span>
    </div>

    <p class="address">Po Box, 456 B Harbor Rd<br>Bayview, CR 40215</p>

    <ul class="contacts">
      <li>
        <svg viewBox="0 0 16 16" aria-hidden="true"><path d="M4 1h8a1 1 0 0 1 1 1v12a1 1 0 0 1-1 1H4a1 1 0 0 1-1-1V2a1 1 0 0 1 1-1zm1 2v9h6V3H5zm3 10a.8.8 0 1 0 0 1.6A.8.8 0 0 0 8 13z"/></svg>
        555.240.3100
      </li>
      <li>
        <svg viewBox="0 0 16 16" aria-hidden="true"><path d="M3.6 1.5l2.3 2.3-1.4 2a9 9 0 0 0 5.7 5.7l2-1.4 2.3 2.3-1.6 2.1C7.4 16 0 8.6.5 3.1z"/></svg>
        +1 555 018 7742
      </li>
      <li>
        <svg viewBox="0 0 16 16" aria-hidden="true"><path d="M1 3h14v10H1zm1.5 1.2V5l5.5 4 5.5-4v-.8z"/></svg>
        info@coastlinepremierretreats.example
      </li>
      <li>
        <svg viewBox="0 0 16 16" aria-hidden="true"><path d="M8 1a7 7 0 1 0 0 14A7 7 0 0 0 8 1zm0 1.5c.8 0 1.8 1.6 2.1 4.5H5.9C6.2 4.1 7.2 2.5 8 2.5zM2.6 9h2.3c.1 1.7.5 3.2 1 4.1A5.5 5.5 0 0 1 2.6 9zm0-2a5.5 5.5 0 0 1 3.3-4.1C5.4 3.8 5 5.3 4.9 7zm5.4 6.5c-.8 0-1.8-1.6-2.1-4.5h4.2c-.3 2.9-1.3 4.5-2.1 4.5zm2.1-.4c.5-.9.9-2.4 1-4.1h2.3a5.5 5.5 0 0 1-3.3 4.1zM11.1 7c-.1-1.7-.5-3.2-1-4.1A5.5 5.5 0 0 1 13.4 7z"/></svg>
        <span>www.<span class="url-domain">coastlinepremierretreats</span>.example</span>
      </li>
    </ul>

    <div class="person">
      <p class="person-name">Marcus Hale</p>
      <p class="person-title">CEO/Founder</p>
    </div>
    <span class="accent-tab"></span>
    <span class="base-band"></span>
  </section>

  <section class="card card-back" aria-label="Business card back">
    <div class="back-brand">
      <span class="brand-mark"></span>
      <span class="brand-name">Coastline Premier Retreats</span>
    </div>
    <p class="tagline">Luxury Hotel &amp; Resort Email Marketing</p>
  </section>

</main>
</body>
</html>
```